BOLD & MINIMALIST DESIGN NEEDED

We want a very bold but minimalistic business card design that is impactful and utilizes both sides of the business card. Our current logo is included for your use.

We want bold fonts and good use of negative space. We don't want the logo to overpower the design.

Target Market(s)

Professionals who are building new commercial buildings.

Industry/Entity Type

Construction

Contact Information for Business Card

Name, Title, email, office phone, cell phone, website

Font styles to use
Serif
Sans Serif

Requirements
Must have
• Bold design!

```html
<!DOCTYPE html>
<html lang="en">
<head>
<meta charset="utf-8">
<title>Ridgeline Design + Build – Business Card</title>
<link href="https://fonts.googleapis.com/css2?family=Roboto:wght@400;900&display=swap" rel="stylesheet">
<style>
  :root {
    --stage: #3a3a3a;
    --card-dark: #1f1f1f;
    --card-light: #ffffff;
    --brand-green: #7cc242;
    --ink: #1c1c1c;
    --ink-soft: #3d3d3d;
    --white: #ffffff;
  }
  * { box-sizing: border-box; margin: 0; padding: 0; }
  html, body {
    width: 1200px; height: 875px; overflow: hidden;
    background: var(--stage);
    font-family: "Roboto", Arial, sans-serif;
  }
  .stage {
    width: 1200px; height: 875px;
    display: flex; align-items: center; justify-content: center; gap: 40px;
  }
  .card {
    width: 540px; height: 310px;
    border-radius: 18px;
    position: relative;
    box-shadow: 0 10px 30px rgba(0,0,0,.35);
  }
  .card--front {
    background: var(--card-dark);
    display: flex; align-items: center; justify-content: center;
  }
  .card--back {
    background: var(--card-light);
    display: flex; align-items: center;
    padding: 0 34px 0 30px;
  }
  .wordmark {
    display: flex; align-items: center; gap: 12px;
    font-weight: 900; letter-spacing: .5px; text-transform: uppercase;
  }
  .wordmark__dot {
    width: 18px; height: 18px; border-radius: 50%;
    background: var(--brand-green); flex: none;
  }
  .card--front .wordmark { color: var(--white); font-size: 30px; }
  .card--back .wordmark { color: var(--ink); font-size: 19px; }
  .back__brand { width: 230px; display: flex; justify-content: center; }
  .divider {
    width: 1px; height: 170px; margin: 0 22px 0 16px;
    background: linear-gradient(to bottom, transparent, var(--brand-green), transparent);
  }
  .contact { color: var(--ink-soft); }
  .contact__name {
    color: var(--brand-green); font-weight: 900; font-size: 22px;
    text-transform: uppercase; line-height: 1.05;
  }
  .contact__title { font-size: 14px; margin-bottom: 16px; }
  .contact__list { list-style: none; font-size: 13px; line-height: 1.7; }
  .contact__list li { display: flex; align-items: center; gap: 7px; }
  .contact__icon { width: 11px; height: 11px; fill: var(--brand-green); flex: none; }
</style>
</head>
<body>
<main class="stage">
  <section class="card card--front" aria-label="Card front">
    <div class="wordmark"><span class="wordmark__dot"></span>Ridgeline Design + Build</div>
  </section>

  <section class="card card--back" aria-label="Card back">
    <div class="back__brand">
      <div class="wordmark"><span class="wordmark__dot"></span>Ridgeline</div>
    </div>
    <div class="divider"></div>
    <div class="contact">
      <h1 class="contact__name">Daniel Marsh</h1>
      <p class="contact__title">Owner/CEO</p>
      <ul class="contact__list">
        <li><svg class="contact__icon" viewBox="0 0 24 24"><path d="M6.6 10.8a15 15 0 0 0 6.6 6.6l2.2-2.2a1 1 0 0 1 1-.25 11.4 11.4 0 0 0 3.6.57 1 1 0 0 1 1 1V20a1 1 0 0 1-1 1A17 17 0 0 1 3 4a1 1 0 0 1 1-1h3.5a1 1 0 0 1 1 1c0 1.25.2 2.45.57 3.57a1 1 0 0 1-.25 1z"/></svg>07 5120 4480</li>
        <li><svg class="contact__icon" viewBox="0 0 24 24"><path d="M7 1h10a2 2 0 0 1 2 2v18a2 2 0 0 1-2 2H7a2 2 0 0 1-2-2V3a2 2 0 0 1 2-2zm0 3v14h10V4z"/></svg>0432 607 915</li>
        <li><svg class="contact__icon" viewBox="0 0 24 24"><path d="M2 5h20v14H2zm2 2v.5l8 5 8-5V7z"/></svg>info@ridgelinebuild.com</li>
        <li><svg class="contact__icon" viewBox="0 0 24 24"><circle cx="12" cy="12" r="10"/></svg>www.ridgelinebuild.com</li>
      </ul>
    </div>
  </section>
</main>
</body>
</html>
```